Business Card for beauty technology startup

Design Glimora Business Card for a Beauty, based on the website identity and colors (https://www.glimora-example.com).
Glimora is a beauty tech startup that gathers helpful product info for beauty lovers and consumers (such as availability on stores, price range and product reviews) for makeup products. The card design must be young, colorful but clean, and very modern.

Target Market(s)

woman, 15-35

Industry/Entity Type

Cosmetics

Contact Information for Business Card

Full Name, address, phone

Font styles to use
Other font styles liked:
• Advent Pro

Colors
e34297
86cfc6
ffffff
5c5c5c
e8e8e8
e667a6
b2b2b2

Requirements
Must have
• One full colored side with a creative design and another with card info
• Use Color palette: #95C5C5 and/or #D38AA5
• Use fonts: Advent Pro
• Use website identity: https://www.glimora-example.com
Nice to have
• If needed extra font: Roboto

```html
<!DOCTYPE html>
<html lang="en">
<head>
<meta charset="utf-8">
<title>Glimora Business Card</title>
<link href="https://fonts.googleapis.com/css2?family=Advent+Pro:wght@300;400;600&display=swap" rel="stylesheet">
<style>
  :root {
    --page-bg: #e6e6e6;
    --card-pink: #c98099;
    --card-pink-deep: #bd7390;
    --card-white: #f7f7f5;
    --logo-ink: #2f2a2d;
    --brand-pink: #b86c8c;
    --icon-teal: #5fa8a6;
    --shadow: rgba(0, 0, 0, 0.18);
  }
  * { box-sizing: border-box; margin: 0; padding: 0; }
  html, body {
    width: 1200px;
    height: 576px;
    overflow: hidden;
    background: var(--page-bg);
    font-family: "Advent Pro", sans-serif;
  }
  .canvas {
    position: relative;
    width: 1200px;
    height: 576px;
  }
  .card {
    position: absolute;
    top: 138px;
    width: 484px;
    height: 294px;
    border-radius: 14px;
    box-shadow: 0 3px 8px var(--shadow);
  }
  .card--front {
    left: 82px;
    background: linear-gradient(180deg, var(--card-pink) 0%, var(--card-pink-deep) 100%);
    display: flex;
    align-items: center;
    justify-content: center;
  }
  .card--back {
    left: 602px;
    width: 480px;
    height: 292px;
    background: var(--card-white);
  }
  .brand {
    display: flex;
    align-items: center;
    gap: 16px;
  }
  .brand__dot {
    border-radius: 50%;
    border: 1.5px solid currentColor;
  }
  .brand__name {
    font-weight: 300;
    text-transform: uppercase;
  }
  .brand--front { color: var(--logo-ink); }
  .brand--front .brand__dot { width: 56px; height: 56px; }
  .brand--front .brand__name { font-size: 44px; letter-spacing: 5px; }
  .brand--back {
    position: absolute;
    top: 38px;
    right: 30px;
    color: var(--brand-pink);
    gap: 10px;
  }
  .brand--back .brand__dot { width: 36px; height: 36px; }
  .brand--back .brand__name { font-size: 28px; letter-spacing: 3px; }
  .holder {
    position: absolute;
    left: 24px;
    top: 160px;
  }
  .holder__name {
    font-size: 22px;
    font-weight: 600;
    color: var(--brand-pink);
    text-transform: uppercase;
    letter-spacing: 0.5px;
    margin-bottom: 8px;
  }
  .contact {
    list-style: none;
  }
  .contact__item {
    display: flex;
    align-items: center;
    gap: 10px;
    font-size: 14px;
    font-weight: 400;
    color: var(--brand-pink);
    line-height: 16.5px;
  }
  .contact__icon {
    width: 11px;
    height: 11px;
    color: var(--icon-teal);
    flex: none;
  }
  .holder__address {
    margin-top: 6px;
    font-size: 14px;
    color: var(--brand-pink);
  }
</style>
</head>
<body>
<main class="canvas">
  <section class="card card--front" aria-label="Card front">
    <div class="brand brand--front">
      <span class="brand__dot"></span>
      <span class="brand__name">Glimora</span>
    </div>
  </section>

  <section class="card card--back" aria-label="Card back">
    <div class="brand brand--back">
      <span class="brand__dot"></span>
      <span class="brand__name">Glimora</span>
    </div>
    <div class="holder">
      <h1 class="holder__name">Mara Ellison</h1>
      <ul class="contact">
        <li class="contact__item">
          <svg class="contact__icon" viewBox="0 0 12 12" fill="none" stroke="currentColor" stroke-width="1.3"><path d="M2.5 1h2l1 2.5-1.3 1a6 6 0 0 0 3.3 3.3l1-1.3L11 7.5v2a1.2 1.2 0 0 1-1.3 1.2A9 9 0 0 1 1.3 2.3 1.2 1.2 0 0 1 2.5 1z"/></svg>
          00 555 010 200
        </li>
        <li class="contact__item">
          <svg class="contact__icon" viewBox="0 0 12 12" fill="none" stroke="currentColor" stroke-width="1.3" stroke-linecap="round"><path d="M5 7l2-2M4.2 5.5 2.8 6.9a2 2 0 0 0 2.8 2.8L7 8.3M7.8 6.5l1.4-1.4a2 2 0 0 0-2.8-2.8L5 3.7"/></svg>
          www.glimora-example.com
        </li>
        <li class="contact__item">
          <svg class="contact__icon" viewBox="0 0 12 12" fill="none" stroke="currentColor" stroke-width="1.2"><rect x="1" y="2.5" width="10" height="7"/><path d="M1 2.5l5 4 5-4"/></svg>
          hello@glimora-example.com
        </li>
      </ul>
      <p class="holder__address">45, Rose Lane, Lumen City, Country - 654321</p>
    </div>
  </section>
</main>
</body>
</html>
```